Course Lantern

CourseLantern.example will be a place for people looking for information, resources, and advisement to start or continue their education. We want a friendly, inviting site design that makes finding what potential students are looking for simple and easy to navigate. We are not committed to the colors of the logo, so variations on the color scheme are welcome.

Text instructions based on the wireframe: For the site's homepage we'd like a banner at the very top for our Logo and white space to the right of it. See attachments for logo + wireframe. Below that would be navigation. Below that split into 2/3 on the left we would have home page content, and 1/3 on the right we would have the lead form. At the bottom of the page we would have a space for types of degrees, then a footer with copyright info + site info.

See wireframes for additional page layouts.

Industry/Entity Type

Education

Requirements
Must have
• At minimum we are looking for three pages: homepage, choose your degree path page, and content page.
Nice to have
• -White space is appreciated
-Variations on the color scheme are welcome, we are not married to the existing logo's color scheme.

```html
<!DOCTYPE html>
<html lang="en">
<head>
<meta charset="utf-8">
<title>Course Lantern</title>
<link rel="stylesheet" href="https://fonts.googleapis.com/css2?family=Ubuntu:wght@400;500&family=Exo+2:ital,wght@0,500;1,500&display=swap">
<style>
:root{
  --orange:#ec6e12;
  --orange-light:#f6a31c;
  --yellow:#fdb913;
  --slate:#2f5563;
  --blue:#1a6fae;
  --text:#3a3a3a;
  --card:#ececec;
  --card-edge:#d6d6d6;
  --page:#ffffff;
}
*{box-sizing:border-box;margin:0;padding:0}
html,body{width:1008px;height:1200px;overflow:hidden;background:var(--page)}
body{font-family:"Ubuntu",sans-serif;color:var(--text);position:relative}
.site-header .brand{position:absolute;left:125px;top:44px;font-family:"Ubuntu",sans-serif;font-weight:500;font-size:38px;color:var(--slate);letter-spacing:-0.5px}
.contact-line{position:absolute;right:116px;font-size:12px;color:var(--blue);font-weight:500;text-align:right}
.contact-line span{color:var(--orange);font-size:16px;margin-left:4px}
.contact-line.phone{top:40px}
.contact-line.mail{top:60px}
.contact-line.mail span{font-style:italic;text-decoration:underline}
.card{position:absolute;left:117px;width:783px;background:var(--card);border:1px solid var(--card-edge);box-shadow:0 2px 4px rgba(0,0,0,.25)}
.card.main{top:102px;height:832px}
.card.degrees{top:953px;height:212px}
.rings{position:absolute;left:-14px;top:0}
.nav{display:flex;margin-left:25px;width:733px;height:47px;border-bottom:1px solid #e2e2e2}
.nav a{flex:1;display:flex;align-items:center;justify-content:center;font-size:12px;font-weight:500;color:var(--orange);text-decoration:none;border-left:1px solid #d4d4d4}
.nav a:last-child{border-right:1px solid #d4d4d4}
.nav a.current{color:var(--blue)}
.hero{position:absolute;left:25px;top:66px;width:732px;height:234px;border:2px solid var(--orange);background:linear-gradient(180deg,#5a7fae 0%,#8fb0d6 45%,#dfe9f3 75%,#b9c9dc 100%)}
.hero-list{position:absolute;left:30px;top:40px;list-style:none}
.hero-list li{position:relative;padding-left:22px;margin-bottom:18px;color:#fff}
.hero-list li::before{content:"";position:absolute;left:2px;top:10px;width:8px;height:8px;border-radius:50%;background:#fff}
.hero-list strong{display:block;font-family:"Exo 2",sans-serif;font-weight:500;font-size:23px;font-variant:small-caps;line-height:1.1;text-shadow:0 1px 2px rgba(0,0,0,.35)}
.hero-list em{font-family:"Exo 2",sans-serif;font-size:12px;font-weight:500;text-shadow:0 1px 2px rgba(0,0,0,.35)}
.badge{position:absolute;width:34px;height:34px;border-radius:50%;background:radial-gradient(circle at 40% 35%,#fff 50%,#ddd);box-shadow:0 2px 3px rgba(0,0,0,.3);color:var(--orange-light);font-family:"Ubuntu",sans-serif;font-size:22px;display:flex;align-items:center;justify-content:center}
.section-title{position:absolute;font-family:"Exo 2",sans-serif;font-style:italic;font-weight:500;font-size:20px;color:var(--orange)}
.rule{position:absolute;height:3px;border-top:2px solid var(--orange);border-bottom:1px solid var(--yellow)}
.copy{position:absolute;font-size:11px;line-height:13.2px;text-align:justify}
.copy p+p{margin-top:13px}
.divider{position:absolute;left:446px;top:316px;width:1px;height:502px;background:#9a9a9a}
.tile{position:absolute;top:742px;width:193px;height:75px;border:2px solid var(--orange);background:#fff;display:flex;align-items:center;justify-content:center}
.tile div{width:80px;height:60px;border-radius:6px}
.lead-intro{position:absolute;left:473px;width:284px;font-size:10px;font-style:italic;line-height:12px}
.lead-intro p+p{margin-top:12px}
.lead-form{position:absolute;left:473px;top:423px;width:284px;height:390px;background:linear-gradient(180deg,var(--yellow) 0%,#fca810 60%,#f28a0c 100%);padding:22px 13px 0 13px}
.lead-form label{display:block;font-size:9.5px;line-height:11px;color:#4a3200;margin-bottom:2px}
.field{height:17px;background:#fff;border:1px solid #e9a21b;font-size:9px;line-height:11px;font-style:italic;color:#a8a8a8;padding:2px 8px;margin-bottom:4px;position:relative}
.field.select::after{content:"";position:absolute;right:0;top:0;width:17px;height:15px;background:var(--orange)}
.field.select::before{content:"";position:absolute;right:5px;top:5px;border:4px solid transparent;border-top:5px solid #fff;z-index:1}
.row{display:flex;gap:4px}
.row .field{flex:none}
.btn{display:inline-block;margin-top:6px;padding:6px 8px;background:var(--yellow);border:1px solid #fff3c4;font-size:11px;color:#4a3200}
.note{font-size:10px;color:#fff;margin-top:6px}
.photo{position:absolute;top:15px;width:365px;height:85px;border:2px solid var(--orange)}
.photo.grads{left:25px;background:linear-gradient(90deg,#111 0%,#6b5343 40%,#9c7b66 60%,#111 100%)}
.photo.faculty{left:400px;background:linear-gradient(90deg,#8a6a44 0%,#c42a2a 30%,#f4f0ee 55%,#c42a2a 80%,#8a6a44 100%)}
.degree-copy{position:absolute;top:154px;width:370px;font-size:10px;line-height:12.3px}
.footer{position:absolute;left:0;width:1008px;top:1172px;text-align:center;font-size:9.5px;color:var(--orange);line-height:12px}
.footer span{color:#555;margin:0 5px}
</style>
</head>
<body>
<header class="site-header">
  <div class="brand">Course Lantern</div>
  <div class="contact-line phone">Call: <span>555-010-0199</span></div>
  <div class="contact-line mail">Email: <span>info@courselantern.example</span></div>
</header>

<section class="card main">
  <svg class="rings" width="28" height="820" viewBox="0 0 28 820" aria-hidden="true">
    <g fill="#9a9a9a" stroke="#777">
      <g transform="translate(0,32)"><line x1="0" y1="2" x2="20" y2="0" stroke-width="2"/><circle cx="22" cy="0" r="4"/></g>
      <g transform="translate(0,186)"><line x1="0" y1="2" x2="20" y2="0" stroke-width="2"/><circle cx="22" cy="0" r="4"/></g>
      <g transform="translate(0,340)"><line x1="0" y1="2" x2="20" y2="0" stroke-width="2"/><circle cx="22" cy="0" r="4"/></g>
      <g transform="translate(0,494)"><line x1="0" y1="2" x2="20" y2="0" stroke-width="2"/><circle cx="22" cy="0" r="4"/></g>
      <g transform="translate(0,648)"><line x1="0" y1="2" x2="20" y2="0" stroke-width="2"/><circle cx="22" cy="0" r="4"/></g>
      <g transform="translate(0,802)"><line x1="0" y1="2" x2="20" y2="0" stroke-width="2"/><circle cx="22" cy="0" r="4"/></g>
    </g>
  </svg>

  <nav class="nav">
    <a class="current" href="#">About Us</a>
    <a href="#">Contact Us</a>
    <a href="#">Privacy Policy</a>
    <a href="#">Terms of Use</a>
    <a href="#">Feed Back</a>
  </nav>

  <div class="hero" role="img" aria-label="Graduates tossing caps into a blue sky with clouds">
    <ul class="hero-list">
      <li><strong>What We Believe</strong><em>Our Staement Of Faith</em></li>
      <li><strong>Degree Programe</strong><em>Degree Worksheets</em></li>
      <li><strong>Visiting Campus</strong><em>Customized Visit</em></li>
    </ul>
  </div>

  <div class="badge" style="left:27px;top:308px">W</div>
  <h2 class="section-title" style="left:75px;top:320px">Welcome to Course Lantern</h2>
  <div class="rule" style="left:25px;top:353px;width:396px"></div>
  <div class="copy" style="left:25px;top:367px;width:396px">
    <p>The Fresh Start Programme is a long term plan for improving the living conditions and prospects for people in the most disadvantaged communities in the Valley Region.</p>
    <p>The programme ensures that the money and support available from the Regional Council and various other publicly funded agencies are targeted at the poorest areas Our role is to coordinate community led regeneration of the area with local residents, through Riverside Partnership Board, seeking cooperation from other organisations within the public, private and voluntary sector to work together with us to tackle many issues that affect the lives of people who live in the area.</p>
    <p>Local transport, access to relevant health care, activities for children and young people, services for the elderly, family support, the environment, education and training opportunities are just some of the issues that have been brought to the attention of Fresh Start of which we are all working on at present.</p>
  </div>

  <div class="badge" style="left:27px;top:615px">S</div>
  <h2 class="section-title" style="left:75px;top:622px">Services</h2>
  <div class="rule" style="left:25px;top:655px;width:396px"></div>
  <div class="copy" style="left:25px;top:674px;width:396px">
    <p>The programme ensures that the money and support available from the Regional Council and various other publicly funded agencies are targeted at the poorest areas Our role is to coordinate community led regeneration of the area with local residents, through Riverside Partnership Board.</p>
  </div>
  <div class="tile" style="left:25px"><div role="img" aria-label="Colourful jigsaw puzzle pieces" style="background:linear-gradient(135deg,#d42a2a,#2a6fd4 40%,#3aa83a 65%,#f2c81a)"></div></div>
  <div class="tile" style="left:229px"><div role="img" aria-label="White jigsaw puzzle with a loose piece" style="background:linear-gradient(135deg,#f4f4f4,#c8c8c8)"></div></div>

  <div class="divider"></div>

  <div class="badge" style="left:498px;top:308px">T</div>
  <h2 class="section-title" style="left:545px;top:320px">Tell us more about YOU!</h2>
  <div class="rule" style="left:473px;top:353px;width:284px"></div>
  <div class="lead-intro" style="top:365px">
    <p>CourseLantern provides you with accredited school information that match your interests.</p>
    <p>Get matched to the right schools today.</p>
  </div>
  <div style="position:absolute;left:473px;top:418px;width:284px;height:1px;background:#c8c8c8"></div>

  <form class="lead-form">
    <label>Subject*</label><div class="field select">Choose One</div>
    <label>Degree Level*</label><div class="field select">Choose One</div>
    <label>High School Grad Yr.*</label><div class="field select">Choose One</div>
    <label>First Name*</label><div class="field">Enter First Name</div>
    <label>Last Name*</label><div class="field">Enter Last Name</div>
    <label>Street Address*</label><div class="field">Enter Street Address</div>
    <label>Zip / City / State*</label>
    <div class="row"><div class="field" style="width:65px"></div><div class="field" style="width:110px"></div><div class="field" style="width:76px"></div></div>
    <label>Phone Number*</label><div class="field">(&nbsp;&nbsp;&nbsp;)</div>
    <label>Email Address*</label><div class="field">Email Address</div>
    <div class="btn">Request Information</div>
    <div class="note">*Required fields</div>
  </form>
</section>

<section class="card degrees">
  <svg class="rings" width="28" height="200" viewBox="0 0 28 200" aria-hidden="true">
    <g fill="#9a9a9a" stroke="#777">
      <g transform="translate(0,30)"><line x1="0" y1="2" x2="20" y2="0" stroke-width="2"/><circle cx="22" cy="0" r="4"/></g>
      <g transform="translate(0,180)"><line x1="0" y1="2" x2="20" y2="0" stroke-width="2"/><circle cx="22" cy="0" r="4"/></g>
    </g>
  </svg>
  <div class="photo grads" role="img" aria-label="Smiling graduates in caps"></div>
  <div class="photo faculty" role="img" aria-label="Faculty group in academic gowns"></div>

  <div class="badge" style="left:25px;top:112px;width:28px;height:28px;font-size:18px">D</div>
  <h3 class="section-title" style="left:59px;top:114px;font-size:17px">Degree Type 1</h3>
  <div class="degree-copy" style="left:25px">CourseLantern helps simplify this process by matching colleges to you and your needs.<br>Tell us about yourself and let us do the work for you.Are you overwhelmed by the thought.</div>

  <div class="badge" style="left:401px;top:112px;width:28px;height:28px;font-size:18px">D</div>
  <h3 class="section-title" style="left:435px;top:114px;font-size:17px">Degree Type 2</h3>
  <div class="degree-copy" style="left:401px">CourseLantern helps simplify this process by matching colleges to you and your needs.<br>Tell us about yourself and let us do the work for you.Are you overwhelmed by the thought.</div>
</section>

<footer class="footer">
  About us<span>|</span>Contact Us<span>|</span>Privacy Policy<span>|</span>Terms of Use<span>|</span>Feed back<br>
  Copyright © 2012. Course Lantern. All Rights Reserved
</footer>
</body>
</html>
```